Bright Path Mentors Needs A New Website Design

We need a 8 page website designed for "Bright Path Mentors .ca" similar in design to: "keystone learning hub .com".

The winner/successful candidate on the home page will be asked to complete the following inner pages to complete the project:

About Us
Philosophy
How We Work
Work With Us
Blog
Find A Tutor
Contact

Target Market(s)

Tutoring business clients/children

Industry/Entity Type

Education

Number of Pages Required

5+ page

Font styles to use
Sans Serif

Requirements
Must have
• The attached logo included of course. Similar design to the design provided above in the brief. Clear high quality high resolution images of children in school settings.

```html
<!DOCTYPE html>
<html lang="en">
<head>
<meta charset="utf-8">
<title>Bright Path Mentors</title>
<link rel="stylesheet" href="https://fonts.googleapis.com/css2?family=Raleway:wght@400;500;600;700&family=Open+Sans:wght@400;600;700&display=swap">
<style>
:root{
  --navy:#2a3592;
  --navy-dark:#1f2878;
  --navy-light:#3c49a8;
  --orange:#f7941d;
  --orange-dark:#e8820c;
  --text:#555b66;
  --muted:#8a8f99;
  --line:#dcdde2;
  --footer:#ebebeb;
  --footer-base:#f3f3f3;
  --white:#ffffff;
}
*{margin:0;padding:0;box-sizing:border-box}
html,body{width:1200px;height:2719px;overflow:hidden;background:var(--white)}
body{position:relative;font-family:"Open Sans",sans-serif;color:var(--text)}
.abs{position:absolute}
h2,h3,.heading{font-family:"Raleway",sans-serif;font-weight:500}

/* header */
.nav-bar{left:0;top:76px;width:1200px;height:47px;background:linear-gradient(#3441a3,var(--navy-dark))}
.nav-item{top:76px;height:47px;line-height:47px;color:var(--white);font-size:14px;font-family:"Raleway",sans-serif;font-weight:500;white-space:nowrap;z-index:3}
.nav-item.active{background:var(--navy-dark);width:72px;left:169px;text-align:center;box-shadow:inset 0 0 0 1px #1a2266}
.brand{left:540px;top:20px;width:120px;height:128px;background:var(--white);display:flex;flex-direction:column;align-items:center;justify-content:center;gap:8px;border-radius:0 0 14px 14px;z-index:5;box-shadow:0 2px 6px rgba(0,0,0,.12)}
.brand-mark{width:34px;height:34px;background:var(--navy);border-radius:50%}
.brand-name{font-family:"Raleway",sans-serif;font-weight:700;font-size:16px;color:var(--navy);text-align:center;line-height:1.15;white-space:nowrap}

/* hero */
.hero{left:0;top:123px;width:1200px;height:450px;background:linear-gradient(100deg,#c9d8ea 0%,#e8eef5 35%,#f4ecdf 60%,#d9e4f0 100%)}
.hero-title{left:0;top:318px;width:1200px;text-align:center;color:var(--white);font-family:"Raleway",sans-serif;font-weight:700;font-size:33px;line-height:34px;text-shadow:0 2px 6px rgba(0,0,0,.35)}
.btn{display:block;text-align:center;font-family:"Raleway",sans-serif;font-weight:700;text-transform:uppercase}
.btn-book{left:531px;top:406px;width:131px;height:36px;line-height:36px;background:var(--orange);color:var(--white);font-size:13px}
.dots{display:flex;gap:6px}
.dot{width:15px;height:15px;border-radius:50%;background:var(--white);border:2px solid var(--white)}
.dot.on{background:var(--orange)}

/* features */
.feature{width:260px;text-align:center}
.feature h3{font-size:20px;color:var(--navy);margin-top:12px}
.feature p{font-size:11.5px;line-height:18px;color:var(--muted);margin:10px auto 0;width:210px}
.btn-outline{margin:14px auto 0;width:112px;height:32px;line-height:28px;border:2px solid var(--navy);color:var(--navy);font-size:11.5px}
.divider{top:584px;width:1px;height:205px;background:var(--line)}

/* how we work */
.how{left:0;top:876px;width:1200px;height:393px;background:linear-gradient(90deg,#ececec 0%,#f2f2f2 45%,#e4e7ec 60%,#d2dae4 100%)}
.section-title{font-size:27px;color:#3a3f4a}
.section-text{font-size:12.5px;line-height:21.5px}
.section-text p+p{margin-top:11px}
.btn-navy{width:112px;height:34px;line-height:34px;background:var(--navy);color:var(--white);font-size:11.5px}

/* philosophy */
.philosophy{left:0;top:1269px;width:1200px;height:399px;background:var(--orange)}

/* video */
.video{left:0;top:1668px;width:1200px;height:371px;background:linear-gradient(90deg,#ead9cf 0%,#f2ece6 40%,#e4e6ec 70%,#d9dfe8 100%)}
.video-veil{left:0;top:1668px;width:1200px;height:371px;background:rgba(255,255,255,.55)}
.player{left:656px;top:1735px;width:357px;height:223px;background:var(--white);box-shadow:0 4px 14px rgba(0,0,0,.3)}
.player-bar{left:656px;top:1930px;width:357px;height:28px;background:#2d2d2d}
.btn-orange{width:107px;height:30px;line-height:30px;background:var(--orange);color:var(--white);font-size:10.5px}

/* testimonials */
.testimonials{left:0;top:2039px;width:1200px;height:321px;background:linear-gradient(var(--navy-light),var(--navy-dark))}
.testi-title{left:0;top:2098px;width:1200px;text-align:center;color:var(--white);font-size:27px}
.testi-quote{left:300px;top:2156px;width:600px;text-align:center;color:#dfe3f7;font-size:15px;line-height:30px}
.testi-quote .mark{font-family:Georgia,serif;font-size:40px;color:var(--white);vertical-align:-12px;line-height:0}
.testi-name{left:0;top:2231px;width:1200px;text-align:center;color:var(--white);font-family:"Raleway",sans-serif;font-size:18px}
.testi-place{left:0;top:2257px;width:1200px;text-align:center;color:var(--white);font-size:10.5px;text-transform:uppercase}
.dots-outline .dot{background:var(--white)}
.dots-outline .dot.first{background:transparent}

/* footer */
.footer{left:0;top:2360px;width:1200px;height:296px;background:var(--footer)}
.footer-col h4{font-family:"Raleway",sans-serif;font-weight:600;font-size:14px;color:#2d3240;text-transform:uppercase;margin-bottom:10px}
.footer-col li{list-style:none;font-size:11px;line-height:21px;color:#5a5f6a;white-space:nowrap}
.social{display:flex;gap:6px}
.social span{width:22px;height:22px;border-radius:50%;background:#7a8090}
.ribbon{left:877px;top:2360px;width:151px;height:236px}
.footer-base{left:0;top:2656px;width:1200px;height:63px;background:var(--footer-base);text-align:center;font-size:11px;line-height:63px;color:#5a5f6a}
</style>
</head>
<body>

<!-- Header -->
<div class="abs nav-bar"></div>
<nav>
  <span class="abs nav-item active">Home</span>
  <span class="abs nav-item" style="left:248px">About Us</span>
  <span class="abs nav-item" style="left:332px">Philosophy</span>
  <span class="abs nav-item" style="left:428px">How We Work</span>
  <span class="abs nav-item" style="left:681px">Work With Us</span>
  <span class="abs nav-item" style="left:794px">Blog</span>
  <span class="abs nav-item" style="left:847px">Find A Tutor</span>
  <span class="abs nav-item" style="left:946px">Contact</span>
</nav>
<div class="abs brand">
  <span class="brand-mark"></span>
  <span class="brand-name">Bright Path<br>Mentors</span>
</div>

<!-- Hero -->
<div class="abs hero" role="img" aria-label="Smiling schoolchildren in a bright classroom with a globe and coloured pencils"></div>
<svg class="abs" style="left:0;top:500px" width="1200" height="80" viewBox="0 0 1200 80" aria-hidden="true">
  <polygon points="0,17 600,64 1200,17 1200,80 0,80" fill="#ffffff"/>
</svg>
<h1 class="abs hero-title">IN-HOME TUTORING BY<br>ONTARIO CERTIFIED TEACHERS</h1>
<a class="abs btn btn-book">Book Now</a>
<div class="abs dots" style="left:563px;top:530px">
  <span class="dot on"></span><span class="dot"></span><span class="dot"></span><span class="dot"></span>
</div>

<!-- Features -->
<div class="abs divider" style="left:464px"></div>
<div class="abs divider" style="left:729px"></div>

<section class="abs feature" style="left:200px;top:600px">
  <svg width="100" height="112" viewBox="0 0 100 112" aria-hidden="true">
    <polygon points="50,3 96,29 96,83 50,109 4,83 4,29" fill="#fff" stroke="#d3d5dc" stroke-width="3"/>
    <polygon points="50,38 78,50 50,62 22,50" fill="var(--navy)"/>
    <path d="M34 56 v12 q16 9 32 0 v-12 l-16 7z" fill="var(--navy)"/>
    <line x1="74" y1="51" x2="74" y2="68" stroke="var(--navy)" stroke-width="2"/>
  </svg>
  <h3>Academic Tutoring</h3>
  <p>Cum sociis natoque penatibus et magnis dis parturient montes nascetu</p>
  <a class="btn btn-outline">Read More</a>
</section>

<section class="abs feature" style="left:461px;top:600px">
  <svg width="100" height="112" viewBox="0 0 100 112" aria-hidden="true">
    <polygon points="50,3 96,29 96,83 50,109 4,83 4,29" fill="#fff" stroke="#d3d5dc" stroke-width="3"/>
    <circle cx="50" cy="45" r="13" fill="var(--navy)"/>
    <path d="M26 80 q0 -20 24 -20 q24 0 24 20z" fill="var(--navy)"/>
  </svg>
  <h3>Our Tutors</h3>
  <p>Cum sociis natoque penatibus et magnis dis parturient montes nascetu</p>
  <a class="btn btn-outline">Read More</a>
</section>

<section class="abs feature" style="left:747px;top:600px">
  <svg width="100" height="112" viewBox="0 0 100 112" aria-hidden="true">
    <polygon points="50,3 96,29 96,83 50,109 4,83 4,29" fill="#fff" stroke="#d3d5dc" stroke-width="3"/>
    <circle cx="46" cy="51" r="16" fill="none" stroke="var(--navy)" stroke-width="4"/>
    <line x1="58" y1="63" x2="72" y2="77" stroke="var(--navy)" stroke-width="6" stroke-linecap="round"/>
  </svg>
  <h3>Find a Tutor</h3>
  <p>Cum sociis natoque penatibus et magnis dis parturient montes nascetu</p>
  <a class="btn btn-outline">Find Now</a>
</section>

<!-- How We Work -->
<div class="abs how"></div>
<div class="abs" style="left:620px;top:876px;width:580px;height:393px;background:linear-gradient(90deg,rgba(236,236,236,1) 0%,rgba(205,214,226,.6) 30%,#c8d2de 100%)" role="img" aria-label="Young boy smiling while writing at a classroom desk"></div>
<h2 class="abs section-title" style="left:176px;top:952px">How We Work</h2>
<div class="abs section-text" style="left:176px;top:1006px;width:460px">
  <p>Bright Path Mentors lays the foundation for student academic achievement with high quality personal tutoring services that build intellectual and personal development in a positive learning environment.</p>
  <p>We provide students customized tutoring instruction that helps them achieve their academic goals. After the students' needs are discussed, we select a tutor that is the best fit for those students then monitor their progress.</p>
</div>
<a class="abs btn btn-navy" style="left:179px;top:1168px">Read More</a>

<!-- Philosophy -->
<div class="abs philosophy"></div>
<svg class="abs" style="left:178px;top:1290px" width="400" height="345" viewBox="0 0 400 345" role="img" aria-label="Classroom photos of children raising hands and writing at their desks">
  <defs>
    <linearGradient id="photoA" x1="0" y1="0" x2="1" y2="1">
      <stop offset="0" stop-color="#e9e2d4"/><stop offset="1" stop-color="#9a8a78"/>
    </linearGradient>
    <linearGradient id="photoB" x1="0" y1="0" x2="1" y2="1">
      <stop offset="0" stop-color="#d7e0c8"/><stop offset="1" stop-color="#7d96a8"/>
    </linearGradient>
  </defs>
  <polygon points="90,5 220,5 270,165 220,330 90,330 8,170" fill="url(#photoA)" stroke="#fff" stroke-width="5" stroke-linejoin="round"/>
  <polygon points="215,95 330,95 390,205 330,312 215,312 160,205" fill="url(#photoB)" stroke="#fff" stroke-width="5" stroke-linejoin="round"/>
</svg>
<h2 class="abs section-title" style="left:596px;top:1351px;color:var(--white)">Philosophy</h2>
<div class="abs section-text" style="left:598px;top:1402px;width:420px;color:#fff6ea">
  <p>Bright Path Mentors lays the foundation for student academic achievement with high quality personal tutoring services that build intellectual and personal development in a positive learning environment.</p>
  <p>We provide students customized tutoring instruction that helps them achieve their academic goals. After the students' needs are discussed, we select a tutor that is the best fit for those students then monitor their progress.</p>
</div>

<!-- Video -->
<div class="abs video" role="img" aria-label="Faded background of happy schoolchildren"></div>
<div class="abs video-veil"></div>
<h2 class="abs section-title" style="left:190px;top:1737px">Watch Our Video</h2>
<div class="abs section-text" style="left:194px;top:1790px;width:430px">
  <p>Bright Path Mentors lays the foundation for student academic achievement with high quality personal tutoring services that build intellectual and personal development in a positive learning environment.</p>
  <p>We provide students customized tutoring instruction that helps them achieve their academic goals.</p>
</div>
<a class="abs btn btn-orange" style="left:192px;top:1926px">Read More</a>
<div class="abs player" role="img" aria-label="Animated explainer video still of a teacher and a drawing hand"></div>
<div class="abs" style="left:656px;top:1735px;width:357px;height:195px;background:linear-gradient(90deg,#f4f4f4,#e6ebee)" role="img" aria-label="Video preview"></div>
<svg class="abs" style="left:807px;top:1820px" width="44" height="44" viewBox="0 0 44 44" aria-hidden="true">
  <circle cx="22" cy="22" r="21" fill="#111"/>
  <polygon points="17,12 33,22 17,32" fill="#fff"/>
</svg>
<div class="abs player-bar"></div>
<svg class="abs" style="left:656px;top:1930px" width="357" height="28" viewBox="0 0 357 28" aria-hidden="true">
  <polygon points="12,9 20,14 12,19" fill="#fff"/>
  <rect x="30" y="12" width="268" height="4" rx="2" fill="#666"/>
  <rect x="30" y="12" width="100" height="4" rx="2" fill="#3a7fd0"/>
  <polygon points="326,11 330,11 334,7 334,21 330,17 326,17" fill="#fff"/>
  <path d="M337 10 q4 4 0 8" stroke="#fff" stroke-width="1.5" fill="none"/>
</svg>

<!-- Testimonials -->
<div class="abs testimonials"></div>
<h2 class="abs testi-title">Testimonials</h2>
<p class="abs testi-quote"><span class="mark">&ldquo;</span> Clara Medina Dear Ms. Medina: RE: Highest Recommendation for Tutoring Services &nbsp;I take this opportunity to give the highest... a <span class="mark">&rdquo;</span></p>
<p class="abs testi-name">Nora P.</p>
<p class="abs testi-place">Vaughan, Ontario</p>
<div class="abs dots dots-outline" style="left:572px;top:2291px;gap:2px">
  <span class="dot first"></span><span class="dot"></span><span class="dot"></span><span class="dot"></span>
</div>

<!-- Footer -->
<footer>
  <div class="abs footer"></div>
  <div class="abs footer-col" style="left:183px;top:2406px">
    <h4>Subjects</h4>
    <ul>
      <li>Elementary Tutoring</li><li>Foreign Languages</li><li>Math Tutoring</li><li>Science Tutoring</li>
      <li>Accounting Tutoring</li><li>Computer Science Tutoring</li><li>View All</li>
    </ul>
  </div>
  <div class="abs footer-col" style="left:380px;top:2406px">
    <h4>Company</h4>
    <ul>
      <li>Jobs</li><li>Privacy Policy</li><li>How We Operate</li><li>Our Guarantee</li><li>Our Tutors</li><li>Pricing</li>
    </ul>
  </div>
  <div class="abs footer-col" style="left:505px;top:2406px">
    <h4>&nbsp;</h4>
    <ul>
      <li>Tutor Selection Process</li><li>Video Overview</li><li>New Client Registration</li><li>New Tutor Registration</li>
      <li>Testimonials</li><li>Client Credit Card Input</li><li>FAQs</li>
    </ul>
  </div>
  <div class="abs footer-col" style="left:676px;top:2406px">
    <h4>Contact Us</h4>
    <ul>
      <li>128 Maple Avenue, Suite 210</li><li>Toronto Ontario M4B 1K2</li><li>1-800-555-0142</li><li>info@brightpathmentors.ca</li>
    </ul>
    <div class="social" style="margin-top:10px" aria-label="Social links">
      <span></span><span></span><span></span><span></span>
    </div>
  </div>
  <svg class="abs ribbon" viewBox="0 0 151 236" aria-hidden="true">
    <polygon points="0,0 151,0 151,236 75,205 0,236" fill="#d5d5d5"/>
    <polygon points="6,0 145,0 145,226 75,198 6,226" fill="#ebebeb" stroke="#cfcfcf" stroke-width="1"/>
  </svg>
  <div class="abs" style="left:877px;top:2435px;width:151px;display:flex;flex-direction:column;align-items:center;gap:10px">
    <span class="brand-mark"></span>
    <span class="brand-name">Bright Path<br>Mentors</span>
  </div>
  <div class="abs footer-base">&copy; 2016 Company Name &nbsp;All right reserved &nbsp;Term of Use</div>
</footer>

</body>
</html>
```